WordPress Site That Reviews Footwear

We need a wordpress web design for an affiliate site called PaceKite. We review and do roundups on footwear products. The final design should be clean and mobile friendly. The site should be built with Gutenberg page builder. We like the design of https://lunavessel.com/.
Updates

Need extra days to review

Target Market(s)

USA

Industry/Entity Type

Footwear

Logo Text

PaceKite

Number of Pages Required

4 page

Font styles to use
Serif
Sans Serif

Requirements
Must have
• Wordpress site
Blog post
Page
Categories
Homepage

```html
<!DOCTYPE html>
<html lang="en">
<head>
<meta charset="utf-8">
<title>PaceKite – Footwear Reviews</title>
<link rel="stylesheet" href="https://fonts.googleapis.com/css2?family=Poppins:wght@700;800&family=Roboto:wght@400;500;700&display=swap">
<style>
:root{
  --navy:#061f4d;
  --teal:#55e6bd;
  --text:#1d2433;
  --muted:#6b7280;
  --card:#e8f4f8;
  --white:#ffffff;
}
*{margin:0;padding:0;box-sizing:border-box}
html,body{width:1200px;height:2777px;overflow:hidden}
body{position:relative;background:var(--white);font-family:'Roboto',Arial,sans-serif;color:var(--text)}
.abs{position:absolute}
.heading{font-family:'Poppins',Arial,sans-serif;font-weight:800;color:var(--navy)}
.center{text-align:center}

/* hero */
.hero{left:0;top:0;width:1200px;height:567px;background:radial-gradient(ellipse at 25% 40%,#dbeff3 0%,#c8e6ee 45%,#a9d4e4 100%)}
.brand{display:flex;align-items:center;gap:12px;font-family:'Poppins',Arial,sans-serif;font-weight:700;font-size:21px;color:var(--navy)}
.brand-dot{width:40px;height:40px;border-radius:50%;background:var(--teal)}
.nav{display:flex;gap:31px;font-size:15.5px;font-weight:500;color:var(--navy)}
.social-top{display:flex;gap:10px}
.social-top span{width:34px;height:34px;border-radius:50%;background:var(--teal)}
.hero-title{font-size:51px;line-height:1}
.hero-text{font-size:17px;line-height:27px;color:var(--navy)}
.btn{display:flex;align-items:center;justify-content:center;gap:8px;background:var(--teal);color:var(--navy);border-radius:30px;font-weight:500;text-transform:uppercase}
.btn svg{flex:none}
.photo-round{border-radius:50%;background:radial-gradient(circle at 50% 50%,#8a5a3c 0%,#5a3a28 60%,#3e2a1e 100%)}
.icon-bubble{width:74px;height:74px;border-radius:50%;background:var(--white);box-shadow:0 4px 12px rgba(6,31,77,.12)}

/* about */
.section-title{font-size:40px;line-height:1.1}
.lead{font-size:14.5px;line-height:24px;color:var(--muted)}
.about-band{left:0;top:771px;width:856px;height:519px;background:var(--navy);border-radius:0 6px 6px 0}
.feature h3{font-family:'Roboto',Arial,sans-serif;font-weight:700;font-size:20px;color:var(--white);margin-bottom:15px}
.feature p{font-size:15px;line-height:22px;color:var(--white);margin-bottom:18px}
.feature .btn{width:163px;height:45px;font-size:14.5px}
.about-photo{left:805px;top:874px;width:395px;height:315px;background:linear-gradient(180deg,#f2bcd0 0%,#f6d0dc 45%,#f4f1ee 70%,#c9c4bd 100%)}

/* advice cards */
.adv-card{top:1506px;width:239px;height:262px;background:var(--card);border-radius:3px}
.adv-icon{position:absolute;left:82px;top:29px;width:75px;height:75px;border-radius:50%;background:var(--teal)}
.adv-card h3{position:absolute;top:127px;width:100%;text-align:center;font-size:18px;font-weight:500;color:var(--navy)}
.adv-card p{position:absolute;top:164px;left:16px;right:16px;text-align:center;font-size:15px;line-height:25px;color:var(--muted)}

/* blog */
.blog-card{top:1908px;width:309px;height:388px;background:var(--white);border-radius:10px;box-shadow:0 3px 18px rgba(6,31,77,.1)}
.blog-photo{position:absolute;left:7px;top:8px;width:295px;height:202px;border-radius:8px}
.blog-date{position:absolute;top:237px;width:100%;display:flex;justify-content:center;align-items:center;gap:6px;font-size:14px;color:var(--teal)}
.blog-card h3{position:absolute;top:260px;width:100%;text-align:center;font-size:18px;font-weight:500;color:var(--navy)}
.blog-card p{position:absolute;top:294px;left:18px;right:18px;text-align:center;font-size:15px;line-height:22px;color:var(--muted)}
.blog-more{position:absolute;top:351px;width:100%;display:flex;justify-content:center;align-items:center;gap:6px;font-size:15px;font-weight:500;color:var(--teal)}

/* footer */
.footer{left:0;top:2377px;width:1200px;height:400px;background:var(--navy)}
.foot-brand{font-family:'Poppins',Arial,sans-serif;font-weight:700;font-size:22px;color:var(--white)}
.foot-social{display:flex;gap:9px}
.foot-social span{width:32px;height:32px;border-radius:50%;border:1.5px solid var(--white)}
.foot-col h4{font-size:17.5px;font-weight:500;color:var(--white);margin-bottom:14px}
.foot-col li{list-style:none;font-size:14px;line-height:26px;color:#d8def0}
.contact-item{display:flex;gap:12px;margin-bottom:10px}
.contact-item b{display:block;font-size:12.5px;font-weight:700;color:var(--white);margin-bottom:3px}
.contact-item span{font-size:14px;line-height:19px;color:#d8def0}
.divider{left:111px;top:2706px;width:978px;height:1px;background:rgba(255,255,255,.15)}
.copyright{top:2731px;width:1200px;font-size:15px;color:#d8def0}
.to-top{left:1105px;top:2686px;width:38px;height:38px;border-radius:50%;background:var(--teal);display:flex;align-items:center;justify-content:center}
</style>
</head>
<body>

<!-- HERO -->
<section class="abs hero"></section>
<div class="abs brand" style="left:113px;top:34px"><span class="brand-dot"></span>PaceKite</div>
<nav class="abs nav" style="left:454px;top:44px"><span>Home</span><span>About Us</span><span>Products</span><span>Review</span><span>Blog</span><span>Contact Us</span></nav>
<div class="abs social-top" style="left:967px;top:37px" aria-label="Social links"><span></span><span></span><span></span></div>

<h1 class="abs heading hero-title" style="left:110px;top:205px">PaceKite</h1>
<p class="abs hero-text" style="left:111px;top:275px;width:460px">Lorem ipsum dolor sit amet, consectetur adipiscing elit, sed do eiusmod tempor incididunt</p>
<a class="abs btn" style="left:111px;top:357px;width:185px;height:49px;font-size:16.5px">Learn More
<svg width="16" height="16" viewBox="0 0 16 16"><circle cx="8" cy="8" r="8" fill="#061f4d"/><path d="M6.5 4.5 10 8l-3.5 3.5" stroke="#55e6bd" stroke-width="2" fill="none"/></svg></a>

<div class="abs photo-round" style="left:660px;top:133px;width:377px;height:377px" role="img" aria-label="Photo of shoes arranged on wooden shelves"></div>
<div class="abs icon-bubble" style="left:736px;top:117px" role="img" aria-label="Shoe review icon"></div>
<div class="abs icon-bubble" style="left:889px;top:117px" role="img" aria-label="Price box icon"></div>
<div class="abs icon-bubble" style="left:637px;top:213px" role="img" aria-label="Sneaker icon"></div>
<div class="abs icon-bubble" style="left:988px;top:213px" role="img" aria-label="Discount icon"></div>
<div class="abs icon-bubble" style="left:637px;top:356px" role="img" aria-label="Rating icon"></div>
<div class="abs icon-bubble" style="left:988px;top:356px" role="img" aria-label="Newsletter icon"></div>
<div class="abs icon-bubble" style="left:736px;top:462px" role="img" aria-label="Customer icon"></div>
<div class="abs icon-bubble" style="left:889px;top:462px" role="img" aria-label="Online deal icon"></div>

<!-- ABOUT -->
<h2 class="abs heading section-title center" style="left:0;top:622px;width:1200px">About Us</h2>
<p class="abs lead center" style="left:0;top:680px;width:1200px">Lorem ipsum dolor sit amet, consectetur adipiscing elit, sed do eiusmod tempor incididunt ut labore et dolore magna aliqua.<br>Ut enim ad minim veniam, quis nostrud exercitation ullamcoaliquip ex ea commodo consequat.</p>

<section class="abs about-band"></section>
<div class="abs feature" style="left:111px;top:854px;width:300px"><h3>Lorem ipsum dolor</h3><p>Sed ut perspiciatis unde omnis iste natus error sit voluptatem accusantium</p><a class="btn">Read More <svg width="13" height="13" viewBox="0 0 16 16"><circle cx="8" cy="8" r="8" fill="#061f4d"/><path d="M6.5 4.5 10 8l-3.5 3.5" stroke="#55e6bd" stroke-width="2" fill="none"/></svg></a></div>
<div class="abs feature" style="left:454px;top:854px;width:300px"><h3>Lorem ipsum dolor</h3><p>Sed ut perspiciatis unde omnis iste natus error sit voluptatem accusantium</p><a class="btn">Read More <svg width="13" height="13" viewBox="0 0 16 16"><circle cx="8" cy="8" r="8" fill="#061f4d"/><path d="M6.5 4.5 10 8l-3.5 3.5" stroke="#55e6bd" stroke-width="2" fill="none"/></svg></a></div>
<div class="abs feature" style="left:111px;top:1060px;width:300px"><h3>Lorem ipsum dolor</h3><p>Sed ut perspiciatis unde omnis iste natus error sit voluptatem accusantium</p><a class="btn">Read More <svg width="13" height="13" viewBox="0 0 16 16"><circle cx="8" cy="8" r="8" fill="#061f4d"/><path d="M6.5 4.5 10 8l-3.5 3.5" stroke="#55e6bd" stroke-width="2" fill="none"/></svg></a></div>
<div class="abs feature" style="left:454px;top:1060px;width:300px"><h3>Lorem ipsum dolor</h3><p>Sed ut perspiciatis unde omnis iste natus error sit voluptatem accusantium</p><a class="btn">Read More <svg width="13" height="13" viewBox="0 0 16 16"><circle cx="8" cy="8" r="8" fill="#061f4d"/><path d="M6.5 4.5 10 8l-3.5 3.5" stroke="#55e6bd" stroke-width="2" fill="none"/></svg></a></div>
<div class="abs about-photo" role="img" aria-label="Photo of a woman on a sofa holding a handbag with high heels lined up on the floor"></div>

<!-- ADVICE -->
<h2 class="abs heading section-title center" style="left:0;top:1383px;width:1200px;line-height:35px">Finally... PaceKite advice that<br>gets results.</h2>
<div class="abs adv-card" style="left:89px"><span class="adv-icon" role="img" aria-label="Boot icon"></span><h3>Lorem ipsum dolor</h3><p>Sed ut perspiciatis unde omnis iste natus error sit voluptatem accusantium totam</p></div>
<div class="abs adv-card" style="left:350px"><span class="adv-icon" role="img" aria-label="Shopping bag icon"></span><h3>Lorem ipsum dolor</h3><p>Sed ut perspiciatis unde omnis iste natus error sit voluptatem accusantium totam</p></div>
<div class="abs adv-card" style="left:610px"><span class="adv-icon" role="img" aria-label="Advisor icon"></span><h3>Lorem ipsum dolor</h3><p>Sed ut perspiciatis unde omnis iste natus error sit voluptatem accusantium totam</p></div>
<div class="abs adv-card" style="left:871px"><span class="adv-icon" role="img" aria-label="Mobile discount icon"></span><h3>Lorem ipsum dolor</h3><p>Sed ut perspiciatis unde omnis iste natus error sit voluptatem accusantium totam</p></div>

<!-- BLOG -->
<h2 class="abs heading section-title center" style="left:0;top:1835px;width:1200px;font-size:43px">Our Blog</h2>
<article class="abs blog-card" style="left:111px">
  <div class="blog-photo" style="background:linear-gradient(160deg,#e8e2da 0%,#c7b8b0 45%,#e38a92 70%,#5a5a5a 100%)" role="img" aria-label="Photo of a runner tying pink sneakers on a yoga mat"></div>
  <div class="blog-date"><svg width="13" height="13" viewBox="0 0 14 14"><rect x="1" y="2.5" width="12" height="10.5" rx="1" fill="none" stroke="#55e6bd" stroke-width="1.5"/><path d="M1 6h12M4 1v3M10 1v3" stroke="#55e6bd" stroke-width="1.5"/></svg>February 2, 2021</div>
  <h3>Lorem ipsum dolor sit amet,</h3>
  <p>Sed ut perspiciatis unde omnis iste natus sit voluptatem accusantium</p>
  <div class="blog-more">READ MORE <svg width="13" height="13" viewBox="0 0 16 16"><circle cx="8" cy="8" r="8" fill="#55e6bd"/><path d="M6.5 4.5 10 8l-3.5 3.5" stroke="#fff" stroke-width="2" fill="none"/></svg></div>
</article>
<article class="abs blog-card" style="left:445px">
  <div class="blog-photo" style="background:linear-gradient(160deg,#3f6b52 0%,#b9b2aa 45%,#e7e4e0 70%,#6a6a6a 100%)" role="img" aria-label="Photo of a woman trying on heels in a shoe store"></div>
  <div class="blog-date"><svg width="13" height="13" viewBox="0 0 14 14"><rect x="1" y="2.5" width="12" height="10.5" rx="1" fill="none" stroke="#55e6bd" stroke-width="1.5"/><path d="M1 6h12M4 1v3M10 1v3" stroke="#55e6bd" stroke-width="1.5"/></svg>February 2, 2021</div>
  <h3>Lorem ipsum dolor sit amet,</h3>
  <p>Sed ut perspiciatis unde omnis iste natus sit voluptatem accusantium</p>
  <div class="blog-more">READ MORE <svg width="13" height="13" viewBox="0 0 16 16"><circle cx="8" cy="8" r="8" fill="#55e6bd"/><path d="M6.5 4.5 10 8l-3.5 3.5" stroke="#fff" stroke-width="2" fill="none"/></svg></div>
</article>
<article class="abs blog-card" style="left:779px">
  <div class="blog-photo" style="background:linear-gradient(160deg,#3c4a66 0%,#8a3a4a 40%,#c23a4e 65%,#8a7556 100%)" role="img" aria-label="Photo of people wearing red and white sneakers on rocks"></div>
  <div class="blog-date"><svg width="13" height="13" viewBox="0 0 14 14"><rect x="1" y="2.5" width="12" height="10.5" rx="1" fill="none" stroke="#55e6bd" stroke-width="1.5"/><path d="M1 6h12M4 1v3M10 1v3" stroke="#55e6bd" stroke-width="1.5"/></svg>February 2, 2021</div>
  <h3>Lorem ipsum dolor sit amet,</h3>
  <p>Sed ut perspiciatis unde omnis iste natus sit voluptatem accusantium</p>
  <div class="blog-more">READ MORE <svg width="13" height="13" viewBox="0 0 16 16"><circle cx="8" cy="8" r="8" fill="#55e6bd"/><path d="M6.5 4.5 10 8l-3.5 3.5" stroke="#fff" stroke-width="2" fill="none"/></svg></div>
</article>

<!-- FOOTER -->
<footer class="abs footer"></footer>
<span class="abs" style="left:227px;top:2494px;width:44px;height:44px;border-radius:50%;background:var(--white)"></span>
<div class="abs foot-brand center" style="left:149px;top:2543px;width:200px">PaceKite</div>
<div class="abs foot-social" style="left:173px;top:2595px" aria-label="Social links"><span></span><span></span><span></span><span></span></div>

<div class="abs foot-col" style="left:444px;top:2470px"><h4>Quick Links</h4><ul><li>Home</li><li>About Us</li><li>Products</li><li>Review</li><li>Blog</li><li>Contact Us</li></ul></div>
<div class="abs foot-col" style="left:645px;top:2470px"><h4>About Company</h4><ul><li>Legal Information</li><li>Terms &amp; Condition</li><li>Privacy Policy</li><li>Site Map</li><li>FAQ</li></ul></div>
<div class="abs foot-col" style="left:853px;top:2470px;width:260px">
  <h4>Contact Us</h4>
  <div class="contact-item"><svg width="14" height="14" viewBox="0 0 14 14" style="margin-top:2px"><path d="M3 1l2.5 3-1.5 1.5c.8 1.8 2.2 3.2 4 4L9.5 8 13 10.5 11.5 13C6 13 1 8 1 2.5z" fill="#55e6bd"/></svg><div><b>Phone</b><span>512.555.0148</span></div></div>
  <div class="contact-item"><svg width="15" height="12" viewBox="0 0 15 12" style="margin-top:3px"><rect width="15" height="12" rx="1.5" fill="#55e6bd"/><path d="M1 2l6.5 5L14 2" stroke="#061f4d" stroke-width="1.3" fill="none"/></svg><div><b>Email</b><span>hello@pacekite.net</span></div></div>
  <div class="contact-item"><svg width="12" height="15" viewBox="0 0 12 15" style="margin-top:2px;margin-left:1px"><path d="M6 0a6 6 0 0 1 6 6c0 4-6 9-6 9S0 10 0 6a6 6 0 0 1 6-6z" fill="#55e6bd"/><circle cx="6" cy="6" r="2.2" fill="#061f4d"/></svg><div><b>Location</b><span>4410 Willow Creek Blvd. Suite 118,<br>Fairview, Tx. 75069</span></div></div>
</div>

<div class="abs divider"></div>
<div class="abs to-top"><svg width="14" height="10" viewBox="0 0 14 10"><path d="M1.5 8.5 7 3l5.5 5.5" stroke="#fff" stroke-width="2" fill="none"/></svg></div>
<p class="abs copyright center" style="left:0">2021 Copyright - &nbsp;PaceKite | All Rights Reserved</p>

</body>
</html>
```